Redesign of business card for Cedar Ridge Mechanical

We are looking for a new design for our business cards for Cedar Ridge Mechanical. We are a plumbing & HVAC construction company, operating on the West Coast of Canada and USA. Logo attached.
Industry/Entity Type
Construction - Plumbing & HVAC
Contact Information for Business Card
Name, address, phone numbers, email, website address
Look and feel
Each slider illustrates characteristics of the customer's brand and the style your logo design should communicate.

```html
<!DOCTYPE html>
<html lang="en">
<head>
<meta charset="utf-8">
<title>Cedar Ridge Mechanical – Business Card</title>
<link href="https://fonts.googleapis.com/css2?family=Montserrat:wght@400;500;700&display=swap" rel="stylesheet">
<style>
  :root {
    --page-bg: #d9d4ce;
    --card-bg: #efebe6;
    --card-edge: #f7f4f0;
    --ink: #141414;
    --ink-soft: #2b2b2b;
  }
  * { box-sizing: border-box; margin: 0; padding: 0; }
  html, body {
    width: 1200px;
    height: 1047px;
    overflow: hidden;
    background: var(--page-bg);
    font-family: "Montserrat", sans-serif;
    color: var(--ink);
  }
  .card {
    position: absolute;
    left: 80px;
    top: 240px;
    width: 1040px;
    height: 566px;
    border-radius: 26px;
    background: var(--card-bg);
    border: 2px solid var(--card-edge);
    box-shadow: 0 10px 30px rgba(0,0,0,0.12);
  }
  .brand {
    position: absolute;
    left: 44px;
    top: 48px;
    display: flex;
    align-items: center;
    gap: 14px;
  }
  .brand-square {
    width: 22px;
    height: 22px;
    background: var(--ink);
  }
  .brand-name {
    font-weight: 700;
    font-size: 24px;
    line-height: 1.15;
    text-transform: uppercase;
    letter-spacing: 0.5px;
    width: 200px;
  }
  .accent-bar {
    position: absolute;
    left: 0;
    top: 240px;
    width: 22px;
    height: 72px;
    background: var(--ink);
  }
  .person-name {
    position: absolute;
    left: 43px;
    top: 238px;
    font-weight: 700;
    font-size: 38px;
    letter-spacing: 1px;
  }
  .person-title {
    position: absolute;
    left: 44px;
    top: 288px;
    font-weight: 500;
    font-size: 24px;
    color: var(--ink-soft);
  }
  .address {
    position: absolute;
    left: 44px;
    top: 340px;
    font-size: 25px;
    line-height: 39px;
    color: var(--ink-soft);
  }
  .contacts {
    position: absolute;
    left: 44px;
    top: 428px;
    list-style: none;
    font-size: 25px;
    line-height: 38px;
    color: var(--ink-soft);
  }
  .contacts li {
    display: flex;
    align-items: center;
    gap: 12px;
  }
  .contacts svg {
    width: 20px;
    height: 20px;
    fill: var(--ink);
  }
  .brand-large {
    position: absolute;
    left: 505px;
    top: 150px;
    width: 520px;
    text-align: center;
    font-weight: 700;
    font-size: 66px;
    line-height: 1.12;
    text-transform: uppercase;
    letter-spacing: 1px;
  }
</style>
</head>
<body>
  <div class="card">
    <div class="brand">
      <span class="brand-square"></span>
      <span class="brand-name">Cedar Ridge Mechanical</span>
    </div>

    <span class="accent-bar"></span>
    <h1 class="person-name">DANIEL HAYES</h1>
    <p class="person-title">Managing Director</p>

    <p class="address">Your address, City<br>State, Zip 1234</p>

    <ul class="contacts">
      <li>
        <svg viewBox="0 0 20 20" aria-hidden="true"><path d="M2 8c0-3 3-5 8-5s8 2 8 5v2h-4V8H6v2H2z M4 11h12l1 6H3z"/></svg>
        123 456 789
      </li>
      <li>
        <svg viewBox="0 0 20 20" aria-hidden="true"><path d="M2 7l8-5 8 5v11H2z M4 8l6 5 6-5v-1l-6 4-6-4z" fill-rule="evenodd"/></svg>
        info@yourmail.com
      </li>
      <li>
        <svg viewBox="0 0 20 20" aria-hidden="true"><circle cx="10" cy="10" r="8"/><path d="M6 6c2 0 3 2 2 3s-3 1-2 3 3 1 3 3M13 4c-1 2 1 3 3 3" stroke="#efebe6" stroke-width="1.6" fill="none"/></svg>
        www.yourwebsite.com
      </li>
    </ul>

    <div class="brand-large">Cedar Ridge<br>Mechanical</div>
  </div>
</body>
</html>
```